New Innovative Counselling and psychotherapy Service needs Business Card design

Keep it simple and professional. On one side, just company name and logo (perhaps in all blue) and maybe a tag line.

On other side (all white) my name and Qualifications in centre

Industry/Entity Type

Health And Wellness

Contact Information for Business Card

Dara Whelby
Counsellor & Psychotherapist
BSc (Psychol.), BA, Dip. (Couns. & Psych.), PG.Cert (CBT), FGTrK, ONRE

I will also require Mobile no, Email and web site address of which I'll pass on to final designer.

Font styles to use
Sans Serif

Requirements
Must have
• My Logo Only and please use the colours in logo that is in it.
Should not have
• Any other images

```html
<!DOCTYPE html>
<html lang="en">
<head>
<meta charset="utf-8">
<title>Harbor Grove – Business Card</title>
<link rel="stylesheet" href="https://fonts.googleapis.com/css2?family=Montserrat:wght@300;400&family=Roboto:wght@400;700&display=swap">
<style>
  :root {
    --backdrop: #3b3b3d;
    --card: #1d1e20;
    --card-edge: #2a2b2e;
    --blue: #3aa8e2;
    --green: #7cc243;
    --white: #f4f4f4;
    --muted: #9c9ea2;
  }
  * { box-sizing: border-box; margin: 0; padding: 0; }
  html, body {
    width: 799px; height: 1200px; overflow: hidden;
    background: var(--backdrop);
    font-family: "Roboto", Arial, sans-serif;
  }
  .sheet {
    position: relative; width: 799px; height: 1200px;
    display: flex; flex-direction: column; align-items: center; justify-content: space-evenly;
  }
  .card {
    position: relative;
    width: 640px; height: 366px;
    background: var(--card);
    border-radius: 22px;
    overflow: hidden;
    box-shadow: 0 14px 30px rgba(0,0,0,.45);
  }
  /* Front */
  .card-front { display: flex; align-items: center; justify-content: center; }
  .front-brand {
    display: flex; align-items: center; gap: 18px;
    font-family: "Montserrat", Arial, sans-serif; font-weight: 300;
    font-size: 46px; color: var(--card-edge);
    color: #4a4c50;
  }
  .front-brand .dot { width: 34px; height: 34px; border-radius: 50%; background: #4a4c50; }

  /* Back */
  .card-back { padding: 38px 40px; }
  .brand {
    display: flex; align-items: center; gap: 16px;
    font-family: "Montserrat", Arial, sans-serif; font-weight: 300;
    font-size: 40px; color: var(--white); letter-spacing: .3px;
  }
  .brand .dot { width: 50px; height: 50px; border-radius: 50%; background: var(--blue); }
  .person { margin-top: 42px; }
  .person-name { font-weight: 700; font-size: 22px; color: var(--blue); }
  .person-role, .person-quals { font-size: 14px; color: var(--white); line-height: 1.35; }
  .contact { list-style: none; margin-top: 16px; }
  .contact li {
    display: flex; align-items: center; gap: 12px;
    font-size: 15px; color: var(--white); line-height: 1.55;
  }
  .contact svg { width: 14px; height: 14px; flex: none; }
  .accent-band {
    position: absolute; left: 0; right: 0; bottom: 0; height: 9px;
    display: flex;
  }
  .accent-band .blue { flex: 1; background: var(--blue); }
  .accent-band .green { flex: 1; background: var(--green); }
</style>
</head>
<body>
<main class="sheet">
  <section class="card card-front" aria-label="Card front">
    <div class="front-brand"><span class="dot"></span>Harbor Grove</div>
  </section>

  <section class="card card-back" aria-label="Card back">
    <div class="brand"><span class="dot"></span>Harbor Grove</div>
    <div class="person">
      <p class="person-name">Dara Whelby</p>
      <p class="person-role">Counsellor &amp; Psychotherapist</p>
      <p class="person-quals">BSc (Psychol.), BA, Dip. (Couns. &amp; Psych.), PG.Cert (CBT), FGTrK, ONRE</p>
    </div>
    <ul class="contact">
      <li>
        <svg viewBox="0 0 16 16" aria-hidden="true"><path fill="#3aa8e2" d="M3 1h3l1.5 4-2 1.3a8 8 0 0 0 4.2 4.2l1.3-2 4 1.5v3a2 2 0 0 1-2 2A13 13 0 0 1 1 3a2 2 0 0 1 2-2z"/></svg>
        1234 567 7890
      </li>
      <li>
        <svg viewBox="0 0 16 16" aria-hidden="true"><rect x="1" y="3" width="14" height="10" rx="1" fill="#7cc243"/><path d="M1.5 3.5 8 9l6.5-5.5" stroke="#1d1e20" stroke-width="1.3" fill="none"/></svg>
        dara.w@HarborGrove.com
      </li>
      <li>
        <svg viewBox="0 0 16 16" aria-hidden="true"><circle cx="8" cy="8" r="6.5" fill="none" stroke="#3aa8e2" stroke-width="1.4"/><ellipse cx="8" cy="8" rx="2.8" ry="6.5" fill="none" stroke="#3aa8e2" stroke-width="1.2"/><path d="M1.5 8h13" stroke="#3aa8e2" stroke-width="1.2"/></svg>
        www.HarborGrove.com
      </li>
    </ul>
    <div class="accent-band"><span class="blue"></span><span class="green"></span></div>
  </section>
</main>
</body>
</html>
```